Web and Logo Design for eCommerce site

We're launching a sister brand and require a full design for the site.

The site must have an established feel and appeal to corporate and institutional buyers.
Updates

Just a note about the wireframe design:

The Search & Rescue / Coast Guard / NVDK, etc. in the header area aren't buttons or menu items, but rather just info (along the lines of a tagline).  Sort of a "who we serve" sort of thing.

Worth noting is that it's specifically geared towards LARGE BUYERS.  For example, a police force buying 200 headlamps and 85 pairs of gloves.  So they'll register + sign in and then add a bunch of items to a RFQ.

Aim for a professional, masculine design.

Target Market(s)

We will be selling outdoor gear to the military, law enforcement, fire and rescue and first responders.

Requirements
Must have
• We require:
- Logo (vector based)

Site:
- template page
* main site template, re-skinned version of our current site
* horizontal drop-down menu
- product listings page
* thumbnail view of products
- product details page
* including elements such as product image, color/size selector, descriptions and specs (again, based loosely on our current website)
- account management page
* illustrating basic data entry styles for text box, buttons, grid, etc.

The site needs to be given a responsive design, so 2 versions of each design should be presented for desktop + mobile views.

Additional funds are available if the designer is able to fully implement the designs into a responsive framework such as bootstrap.

Nice to have
• Clean, professional design similar to:

http://military.trailvexagear.com/gov/accessories/gloves.html

http://leaf.ombrivo.com/ProductFind.aspx?language=EN&category=Hardshell&subcat=Waterproof_Jackets

```html
<!DOCTYPE html>
<html lang="en">
<head>
<meta charset="utf-8">
<title>Ridgeline – Army Parka with Liner Olive</title>
<link href="https://fonts.googleapis.com/css2?family=Open+Sans:wght@400;600;700&display=swap" rel="stylesheet">
<style>
:root{
  --ink:#1f252b;
  --footer:#15110c;
  --page:#dbe5e7;
  --olive:#a3ae5c;
  --olive-dark:#5d6b3c;
  --red:#c4161c;
  --text:#333;
  --muted:#555;
  --line:#d9d9d9;
  --field:#e8e6e6;
}
*{box-sizing:border-box;margin:0;padding:0}
html,body{width:1200px;height:1182px;overflow:hidden}
body{font-family:"Open Sans",sans-serif;color:var(--text);background:var(--page);position:relative}
a{color:inherit}
.abs{position:absolute}

.topbar{left:0;top:0;width:1200px;height:34px;background:var(--ink);color:#fff;font-size:11px}
.served{left:110px;top:10px;display:flex;gap:0;letter-spacing:.1px}
.served span{padding:0 13px}
.served span:first-child{padding-left:0}
.served i{font-style:normal;opacity:.8}
.social{right:110px;top:6px;display:flex;gap:7px}
.social b{width:20px;height:20px;border-radius:50%;background:#fff;display:block}

.header{left:0;top:34px;width:1200px;height:83px;background:#fff}
.brand{left:112px;top:12px;display:flex;align-items:center;gap:10px}
.brand .mark{width:58px;height:58px;background:var(--olive-dark)}
.brand .name{font-size:32px;font-weight:700;color:#2b3320;letter-spacing:1px;line-height:1}
.brand .tag{font-size:11px;color:#2b3320;letter-spacing:1px;margin-top:4px}
.contact{right:110px;top:32px;display:flex;align-items:center;gap:10px;font-size:13px;color:#666}
.contact svg{display:block}

.mainnav{left:110px;top:118px;width:980px;height:42px;background:var(--ink);display:flex;align-items:center;padding-left:21px;font-size:14px;color:var(--olive)}
.mainnav span{margin-right:29px}
.mainnav .active{color:#fff}
.searchbtn{right:14px;top:8px;width:26px;height:24px;background:var(--olive);display:flex;align-items:center;justify-content:center}

.content{left:110px;top:169px;width:980px;height:645px;background:#fff}
.crumbs{left:18px;top:21px;font-size:13px;color:#222}
.crumbs a{text-decoration:underline}
.crumbs em{font-style:normal;margin:0 6px}
.photo{left:16px;top:62px;width:438px;height:422px;border:1px solid #e2e2e2;padding:6px}
.photo .fill,.thumb{background:radial-gradient(ellipse at 50% 50%,#b08e62 0%,#a68458 45%,#fff 72%)}
.photo .fill{width:100%;height:100%}
.thumb{top:501px;width:66px;height:63px;border:1px solid #ddd}
.arrow{top:524px;width:0;height:0;border-top:7px solid transparent;border-bottom:7px solid transparent}
.arrow.l{left:85px;border-right:9px solid var(--olive-dark)}
.arrow.r{left:353px;border-left:9px solid var(--olive-dark)}

.title{left:489px;top:55px;font-size:27px;font-weight:600;color:#111}
.desc{left:489px;top:102px;width:450px;font-size:12.5px;line-height:20px;color:var(--muted)}
.more{left:489px;top:191px;font-size:11.5px;color:var(--olive-dark)}
.more a{text-decoration:underline}
.price{top:229px}
.price .lbl{font-size:15.5px}
.price .val{font-size:29px;font-weight:600;line-height:32px}
.retail{left:490px;color:var(--olive-dark)}
.yours{left:606px;padding-left:17px;border-left:1px solid #e3e3e3;color:var(--red)}
.yours .lbl,.yours .val{color:var(--red)}
.ship{left:785px;top:229px;padding-left:21px;border-left:1px solid #e3e3e3;font-size:11.5px;line-height:20px;color:#222;height:60px}

.sizes{left:489px;top:309px;width:435px;border:1px solid #ccc;border-collapse:collapse;font-size:13px}
.sizes th{background:var(--ink);color:#fff;height:33px;font-weight:600}
.sizes th+th,.sizes td+td{border-left:1px solid #ccc}
.sizes td{height:30px;border-top:1px solid #e2e2e2;text-align:center;color:#222}
.sizes td:first-child{text-align:left;padding-left:18px;width:228px}
.box{display:inline-block;width:12px;height:12px;border:1px solid #999;background:linear-gradient(#fff,#e6e6e6);vertical-align:middle}

.qty{left:490px;top:492px;width:100px;height:42px;border:1px solid #ccc;font-size:13px;color:#333;display:flex;align-items:center;padding-left:10px;gap:13px}
.qty .dd{width:16px;height:16px;border:1px solid #777;display:flex;align-items:center;justify-content:center}
.rfq{left:610px;top:492px;width:139px;height:42px;background:linear-gradient(#d52129,#b3121a);border:1px solid #9a0f14;color:#fff;font-size:18px;font-weight:600;display:flex;align-items:center;justify-content:center}
.rule{left:494px;top:552px;width:431px;height:1px;background:#e6e6e6}
.share{left:493px;top:580px;display:flex;gap:12px;font-size:11px}
.share .btn{display:flex;align-items:center;gap:4px}
.share .pill{height:19px;border:1px solid #ccc;border-radius:2px;padding:0 6px;display:flex;align-items:center;font-weight:600;color:#333;background:#f4f4f4}
.share .pill.blue{background:#3b5998;color:#fff;border-color:#3b5998}
.share .count{height:19px;border:1px solid #ccc;padding:0 5px;display:flex;align-items:center;color:#555}

.footer{left:0;top:842px;width:1200px;height:340px;background:var(--footer);color:#d6d3cf}
.footer h3{font-size:16.5px;font-weight:600;color:#f2f2f2}
.col{top:37px}
.col ul{list-style:none;margin-top:26px;font-size:13px;line-height:22px}
.offer p{margin-top:25px;font-size:12.5px;line-height:19px;width:260px;color:#bdb9b4}
.mail{margin-top:18px;display:flex;height:38px;width:252px}
.mail span{flex:1;background:#fff;color:#aaa;font-size:13px;display:flex;align-items:center;padding-left:10px}
.mail b{width:61px;background:#d4d4d4;color:#333;font-weight:400;font-size:14px;display:flex;align-items:center;justify-content:center}
.field{left:868px;width:220px;background:var(--field);color:#222;font-size:11.5px;padding:5px 12px}
.submit{left:866px;top:250px;width:86px;height:23px;background:#8e9b4d;color:#fff;font-size:12px;display:flex;align-items:center;justify-content:center}
.copy{left:0;width:1230px;top:294px;text-align:center;font-size:13px;color:#eee}
</style>
</head>
<body>

<div class="abs topbar">
  <div class="abs served"><span>SEARCH &amp;RECUE</span><i>|</i><span>COAST GUARD</span><i>|</i><span>NVDK</span><i>|</i><span>FIRE</span><i>|</i><span>MILIATRY</span><i>|</i><span>LAW ENFORCEMENT</span></div>
  <div class="abs social"><b></b><b></b><b></b><b></b></div>
</div>

<div class="abs header">
  <div class="abs brand">
    <div class="mark"></div>
    <div><div class="name">Ridgeline</div><div class="tag">CANADIAN OUTDOOR PRO SUPPLY</div></div>
  </div>
  <div class="abs contact">
    <svg width="18" height="18" viewBox="0 0 18 18"><path d="M4 1l3 4-2 2c1 3 3 5 6 6l2-2 4 3-2 3C8 17 1 10 1 3z" fill="#999"/></svg>
    <span>Call (+) 0800.555.019</span>
    <svg width="18" height="16" viewBox="0 0 18 16" style="margin-left:4px"><path d="M1 5h16l-2 9H3z M5 5l4-4 4 4" fill="none" stroke="#888" stroke-width="1.6"/></svg>
    <span>(0 item) - $0.00</span>
    <svg width="8" height="6" viewBox="0 0 8 6"><path d="M0 0h8L4 6z" fill="#777"/></svg>
  </div>
</div>

<nav class="abs mainnav">
  <span class="active">RESCUE GEAR</span><span>FOOTWEAR</span><span>CLOTHING</span><span>TENTS MATS SLEEPING BAGS</span><span>CAMPING GEAR</span><span>SNOW SPORTS</span><span>BRAND'S</span>
  <div class="abs searchbtn"><svg width="14" height="14" viewBox="0 0 14 14"><circle cx="6" cy="6" r="4.3" fill="none" stroke="#fff" stroke-width="1.8"/><path d="M9 9l4 4" stroke="#fff" stroke-width="2"/></svg></div>
</nav>

<main class="abs content">
  <div class="abs crumbs"><a>Rescue Gear</a><em>&gt;</em><a>Helmet</a><em>&gt;</em><a>Maze Helmet </a></div>
  <div class="abs photo"><div class="fill" role="img" aria-label="Tan long-sleeve field shirt laid flat"></div></div>
  <div class="abs arrow l"></div>
  <div class="abs thumb" style="left:119px" role="img" aria-label="Shirt thumbnail front"></div>
  <div class="abs thumb" style="left:192px" role="img" aria-label="Shirt thumbnail angle"></div>
  <div class="abs thumb" style="left:265px" role="img" aria-label="Shirt thumbnail detail"></div>
  <div class="abs arrow r"></div>

  <h1 class="abs title">Army Parka with Liner Olive</h1>
  <p class="abs desc">All the actual measurements given on the site as "armpit to armpit x 2" refer to the measurements of the garment and not the size it will fit.<br>The best way of checking if an item will fit is to measure a similar garment you have which fits well and compare the measurements.</p>
  <div class="abs more">+ <a>more</a></div>

  <div class="abs price retail"><div class="lbl">RETAIL PRICE</div><div class="val">$199.99</div></div>
  <div class="abs price yours"><div class="lbl">YOUR PRICE LEVEL</div><div class="val">$150.99</div></div>
  <div class="abs ship">Free Canada Shipping<br>In Stock<br>Ship in 24 hours</div>

  <table class="abs sizes">
    <tr><th></th><th>S</th><th>M</th><th>L</th><th>XL</th></tr>
    <tr><td>Orange</td><td><i class="box"></i></td><td><i class="box"></i></td><td><i class="box"></i></td><td><i class="box"></i></td></tr>
    <tr><td>Grey</td><td><i class="box"></i></td><td><i class="box"></i></td><td><i class="box"></i></td><td><i class="box"></i></td></tr>
    <tr><td>Yellow</td><td><i class="box"></i></td><td><i class="box"></i></td><td><i class="box"></i></td><td><i class="box"></i></td></tr>
    <tr><td>Red</td><td><i class="box"></i></td><td><i class="box"></i></td><td><i class="box"></i></td><td><i class="box"></i></td></tr>
  </table>

  <div class="abs qty">Quantity <span class="dd"><svg width="8" height="5" viewBox="0 0 8 5"><path d="M0 0h8L4 5z" fill="#333"/></svg></span></div>
  <div class="abs rfq">ADD TO RFQ</div>
  <div class="abs rule"></div>
  <div class="abs share">
    <div class="btn"><span class="pill blue">Like</span><span class="count">0</span></div>
    <div class="btn"><span class="pill">Post</span><span class="count">0</span></div>
    <div class="btn"><span class="pill">+1</span><span class="count">0</span></div>
    <div class="btn"><span class="pill">Save</span></div>
  </div>
</main>

<footer class="abs footer">
  <div class="abs col" style="left:112px"><h3>Navigation</h3>
    <ul><li>Rescue Gear</li><li>Footwear</li><li>Clothing</li><li>Tents Mats</li><li>Sleeping Bags</li><li>Camping Gear</li><li>Snow Sports</li><li>Brands</li></ul></div>
  <div class="abs col" style="left:311px"><h3>Products</h3>
    <ul><li>Rescue Gear</li><li>Footwear</li><li>Clothing</li><li>Tents Mats</li><li>Sleeping Bags</li><li>Camping Gear</li><li>Snow Sports</li><li>Brands</li></ul></div>
  <div class="abs col offer" style="left:496px"><h3>Get informed for our Special offers</h3>
    <p>Get the best and most interesting discount offers via email.</p>
    <div class="mail"><span>you@example.com</span><b>Enter</b></div></div>
  <div class="abs col" style="left:867px"><h3>Quick Contact</h3></div>
  <div class="abs field" style="top:76px;height:24px">Name:</div>
  <div class="abs field" style="top:108px;height:24px">Email:</div>
  <div class="abs field" style="top:140px;height:24px">Phone:</div>
  <div class="abs field" style="top:173px;height:66px;padding-top:7px">Message:</div>
  <div class="abs submit">SUMBIT</div>
  <div class="abs copy">CopyRight © 2014 RIDGELINE All Received</div>
</footer>

</body>
</html>
```